Business card for Luxury Portable Restroom Trailer company

We are a Luxury Portable Restroom Trailer Company Called FALCRIDGE HIRES. Based in Orange County California. We provide portable restroom trailers for events, such as, Weddings, Concerts, Charity events, Sporting events, Tournaments, Corporate events, ect. We rent and Sell the Luxury restrooms. Our colors are white, grey, and Orange. As you will see in the logo we uploaded.
There are 2 people in the company so the names and titles will change for the 3 people but card will remain the same. Here is the information for each Person: Dwight Penner CFO 555 318-0476
next Person: Leon Marchetti VP 555 318-0476
Next Person: Owen Marchetti CEO 555 318-0476
Information to include on the card: Luxury Restroom Trailers Rental and Sales. Weddings, Concerts, Charity, Sporting and Corp. Events.

```html
<!DOCTYPE html>
<html lang="en">
<head>
<meta charset="utf-8">
<title>Falcridge Hires – Business Card</title>
<link rel="stylesheet" href="https://fonts.googleapis.com/css2?family=Montserrat:wght@400;500;800&display=swap">
<style>
  :root {
    --bg: #2a2a2c;
    --card: #ffffff;
    --grey: #58585a;
    --orange: #f26a21;
    --ink: #1d1d1f;
  }
  * { box-sizing: border-box; margin: 0; padding: 0; }
  html, body { width: 1200px; height: 880px; overflow: hidden; }
  body {
    background: var(--bg);
    font-family: "Montserrat", Arial, sans-serif;
    position: relative;
  }
  .card {
    position: absolute;
    left: 255px;
    width: 690px;
    height: 394px;
    background: var(--card);
    box-shadow: 0 6px 18px rgba(0,0,0,.45);
  }
  .card--front { top: 34px; }
  .card--back { top: 452px; }

  .brand {
    display: flex;
    align-items: center;
    gap: 14px;
    font-weight: 800;
    color: var(--grey);
    letter-spacing: 1px;
    white-space: nowrap;
  }
  .brand__dot { background: var(--orange); flex: none; }

  .card--front .brand {
    position: absolute;
    left: 0; right: 0; top: 110px;
    justify-content: center;
    font-size: 46px;
  }
  .card--front .brand__dot { width: 30px; height: 30px; }

  .services {
    position: absolute;
    left: 0; right: 0; top: 210px;
    text-align: center;
    color: var(--ink);
    font-size: 17px;
    line-height: 1.9;
    font-weight: 500;
  }
  .services .bullet {
    display: inline-block;
    width: 9px; height: 9px;
    border-radius: 50%;
    background: var(--orange);
    margin: 0 8px 2px 10px;
    vertical-align: middle;
  }

  .card--back .brand {
    position: absolute;
    left: 40px; top: 176px;
    font-size: 26px;
    gap: 10px;
  }
  .card--back .brand__dot { width: 18px; height: 18px; }

  .contacts {
    position: absolute;
    left: 392px; top: 48px; bottom: 48px;
    border-left: 2px solid var(--orange);
    padding-left: 26px;
    display: flex;
    flex-direction: column;
    justify-content: space-between;
  }
  .contact__name {
    color: var(--orange);
    font-weight: 800;
    font-size: 19px;
    text-transform: uppercase;
    letter-spacing: .3px;
  }
  .contact__title { color: var(--ink); font-size: 14px; margin-top: 3px; }
  .contact__phone {
    display: flex; align-items: center; gap: 8px;
    color: var(--ink); font-size: 14px; margin-top: 3px;
  }
  .contact__phone svg { width: 14px; height: 14px; fill: var(--orange); }
</style>
</head>
<body>
  <section class="card card--front">
    <div class="brand"><span class="brand__dot"></span>FALCRIDGE HIRES</div>
    <p class="services">
      <span class="bullet"></span>Luxury Restroom Trailers Rental and Sales<br>
      <span class="bullet"></span>Weddings <span class="bullet"></span>Concerts
      <span class="bullet"></span>Charity <span class="bullet"></span>Sporting and Corp
      <span class="bullet"></span>Events
    </p>
  </section>

  <section class="card card--back">
    <div class="brand"><span class="brand__dot"></span>FALCRIDGE HIRES</div>
    <div class="contacts">
      <div class="contact">
        <div class="contact__name">Dwight Penner</div>
        <div class="contact__title">CFO</div>
        <div class="contact__phone"><svg viewBox="0 0 24 24" aria-hidden="true"><path d="M6.6 10.8a15.1 15.1 0 0 0 6.6 6.6l2.2-2.2a1 1 0 0 1 1-.25 11.4 11.4 0 0 0 3.6.57 1 1 0 0 1 1 1V20a1 1 0 0 1-1 1A17 17 0 0 1 3 4a1 1 0 0 1 1-1h3.5a1 1 0 0 1 1 1c0 1.25.2 2.45.57 3.57a1 1 0 0 1-.25 1z"/></svg>555 318-0476</div>
      </div>
      <div class="contact">
        <div class="contact__name">Leon Marchetti</div>
        <div class="contact__title">VP</div>
        <div class="contact__phone"><svg viewBox="0 0 24 24" aria-hidden="true"><path d="M6.6 10.8a15.1 15.1 0 0 0 6.6 6.6l2.2-2.2a1 1 0 0 1 1-.25 11.4 11.4 0 0 0 3.6.57 1 1 0 0 1 1 1V20a1 1 0 0 1-1 1A17 17 0 0 1 3 4a1 1 0 0 1 1-1h3.5a1 1 0 0 1 1 1c0 1.25.2 2.450.57 3.57a1 1 0 0 1-.25 1z"/></svg>555 318-0476</div>
      </div>
      <div class="contact">
        <div class="contact__name">Owen Marchetti</div>
        <div class="contact__title">CEO</div>
        <div class="contact__phone"><svg viewBox="0 0 24 24" aria-hidden="true"><path d="M6.6 10.8a15.1 15.1 0 0 0 6.6 6.6l2.2-2.2a1 1 0 0 1 1-.25 11.4 11.4 0 0 0 3.6.57 1 1 0 0 1 1 1V20a1 1 0 0 1-1 1A17 17 0 0 1 3 4a1 1 0 0 1 1-1h3.5a1 1 0 0 1 1 1c0 1.25.2 2.45.57 3.57a1 1 0 0 1-.25 1z"/></svg>555 318-0476</div>
      </div>
    </div>
  </section>
</body>
</html>
```